Business Card Design needed for start up company Halvora

In need of a new business card designed for a start up company based in Sydney, Halvora is a new start up innovative Company, our mission it to make property accessible for everyday Australian and to become the leading Real Estate platform in Australia. We want it to be fresh and clean.

Industry/Entity Type

Financial

Contact Information for Business Card

Section for Name
Section for Title

HALVORA - The Strength of Pooling
Mobile:
Direct:

Font styles to use
Sans Serif

Colors
33a6d7
0692cd
0255a3
ffffff

Requirements
Must have
• Logo, all business card details

```html
<!DOCTYPE html>
<html lang="en">
<head>
<meta charset="utf-8">
<title>Halvora Business Card</title>
<link rel="stylesheet" href="https://fonts.googleapis.com/css2?family=Roboto:wght@400;500;700;900&family=Roboto+Condensed:wght@700&display=swap">
<style>
  :root {
    --stage-bg: #2b2b2d;
    --card-bg: #1d1d1f;
    --brand-sky: #33a6d7;
    --brand-blue: #0692cd;
    --brand-deep: #2a5db8;
    --ink-white: #ffffff;
    --rule: #8a8a8e;
  }
  * { margin: 0; padding: 0; box-sizing: border-box; }
  html, body { width: 1200px; height: 900px; overflow: hidden; }
  body {
    background: var(--stage-bg);
    font-family: "Roboto", Arial, sans-serif;
    display: flex;
    flex-direction: column;
    align-items: center;
    justify-content: center;
    gap: 40px;
  }
  .card {
    width: 640px;
    height: 366px;
    background: var(--card-bg);
    border-radius: 3px;
    box-shadow: 0 10px 28px rgba(0,0,0,0.45);
    position: relative;
    color: var(--ink-white);
  }
  /* Front */
  .card-front {
    display: flex;
    flex-direction: column;
    align-items: center;
    justify-content: center;
  }
  .brand-name {
    font-family: "Roboto", Arial, sans-serif;
    font-weight: 900;
    font-size: 64px;
    letter-spacing: 1px;
    color: var(--brand-blue);
    line-height: 1;
  }
  .tagline {
    margin-top: 48px;
    font-size: 17px;
    font-weight: 400;
    letter-spacing: 0.3px;
  }
  /* Back */
  .identity {
    position: absolute;
    right: 322px;
    top: 146px;
    text-align: right;
  }
  .person-name {
    font-family: "Roboto Condensed", Arial, sans-serif;
    font-weight: 700;
    font-size: 31px;
    color: var(--brand-deep);
    line-height: 1;
    white-space: nowrap;
  }
  .person-title {
    margin-top: 6px;
    font-weight: 500;
    font-size: 15px;
    color: var(--brand-sky);
    letter-spacing: 0.3px;
  }
  .divider {
    position: absolute;
    left: 336px;
    top: 136px;
    width: 2px;
    height: 96px;
    background: linear-gradient(to bottom, transparent, var(--rule) 25%, var(--ink-white) 50%, var(--rule) 75%, transparent);
  }
  .contact-list {
    position: absolute;
    left: 356px;
    top: 144px;
    list-style: none;
  }
  .contact-list li {
    display: flex;
    align-items: center;
    gap: 10px;
    font-size: 15px;
    font-weight: 500;
    height: 20px;
    white-space: nowrap;
  }
  .icon { width: 14px; height: 14px; fill: var(--brand-deep); flex: none; }
  .address {
    position: absolute;
    left: 0;
    right: 0;
    bottom: 62px;
    display: flex;
    justify-content: center;
    align-items: center;
    gap: 8px;
    font-size: 16px;
    font-weight: 500;
  }
</style>
</head>
<body>
  <section class="card card-front" aria-label="Card front">
    <h2 class="brand-name">HALVORA</h2>
    <p class="tagline">The Strength of Pooling</p>
  </section>

  <section class="card card-back" aria-label="Card back">
    <div class="identity">
      <h1 class="person-name">DANIEL REEVES</h1>
      <p class="person-title">CEO/FOUNDER</p>
    </div>
    <span class="divider"></span>
    <ul class="contact-list">
      <li>
        <svg class="icon" viewBox="0 0 24 24"><path d="M6.6 10.8a15 15 0 0 0 6.6 6.6l2.2-2.2c.3-.3.7-.4 1-.2 1.1.4 2.3.6 3.6.6.6 0 1 .4 1 1V20c0 .6-.4 1-1 1C10.6 21 3 13.4 3 4c0-.6.4-1 1-1h3.5c.6 0 1 .4 1 1 0 1.3.2 2.5.6 3.6.1.3 0 .7-.2 1z"/></svg>
        <span>612 804 3317</span>
      </li>
      <li>
        <svg class="icon" viewBox="0 0 24 24"><path d="M7 1h10a2 2 0 0 1 2 2v18a2 2 0 0 1-2 2H7a2 2 0 0 1-2-2V3a2 2 0 0 1 2-2zm0 3v15h10V4z"/></svg>
        <span>704 215 8846</span>
      </li>
      <li>
        <svg class="icon" viewBox="0 0 24 24"><path d="M2 5h20v14H2zm2 2v.5l8 5 8-5V7zm0 2.9V17h16V9.9l-8 5z"/></svg>
        <span>daniel@halvora.com</span>
      </li>
      <li>
        <svg class="icon" viewBox="0 0 24 24"><circle cx="12" cy="12" r="10"/><path d="M7 8c2 0 3 1 3 3s2 2 2 4-1 3-1 5M15 4c0 2 1 3 3 3s2 2 3 3" stroke="#1d1d1f" stroke-width="2" fill="none"/></svg>
        <span>www.halvora.com</span>
      </li>
    </ul>
    <p class="address">
      <svg class="icon" viewBox="0 0 24 24" style="height:18px"><path d="M12 1a8 8 0 0 0-8 8c0 6 8 14 8 14s8-8 8-14a8 8 0 0 0-8-8zm0 11a3 3 0 1 1 0-6 3 3 0 0 1 0 6z"/></svg>
      <span>42 Wattle Street, Ultimo, Sydney 2007</span>
    </p>
  </section>
</body>
</html>
```